BUN AND BITE WALL POSTER

Hi designer,

I would like to create a poster to put on my wall.

My intention is to place a bicycle onto a wall and have these words vinyl stick next to it.

" Life is not a race.
It is a journey
Enjoy each moment. Relax!
Have a bowl of Bun and Bite
Make all your dreams come true "

I like traditional fonts - easy to read. See example. This is something I would love.

It will be on a white wall so black text would be ok. I have also attached my logo - maybe try include Bun and Bite font in your design if possible - but not important.

Good luck everyone.

Font styles to use
Decorative
Script

Requirements
Must have
• The placement of my bike will be on the top left corner of the wall so I think it will be best fit if all designs are done in horizontal rectangular shape (landscape)

```html
<!DOCTYPE html>
<html lang="en">
<head>
<meta charset="utf-8">
<title>Bun and Bite Wall Poster</title>
<link rel="stylesheet" href="https://fonts.googleapis.com/css2?family=Cinzel:wght@700&family=Libre+Baskerville:wght@700&family=Yesteryear&display=swap">
<style>
  :root {
    --wall: #ffffff;
    --ink: #111111;
    --bike-dark: #2a2a2a;
    --bike-light: #9a9a9a;
  }
  html, body {
    margin: 0;
    padding: 0;
    width: 1200px;
    height: 1000px;
    overflow: hidden;
    background: var(--wall);
  }
  .poster {
    position: relative;
    width: 1200px;
    height: 1000px;
    background: var(--wall);
    color: var(--ink);
  }
  .bicycle {
    position: absolute;
    left: 15px;
    top: 10px;
    width: 720px;
    height: 515px;
    background: radial-gradient(ellipse at 50% 55%, var(--bike-light) 0%, var(--bike-dark) 100%);
    opacity: 0.85;
    clip-path: polygon(0 0, 720px 0, 720px 440px, 285px 440px, 285px 515px, 0 515px);
  }
  .quote {
    position: absolute;
    left: 200px;
    width: 936px;
    margin: 0;
    text-align: center;
    white-space: nowrap;
  }
  .quote--caps {
    font-family: "Cinzel", serif;
    font-weight: 700;
  }
  .quote--race {
    top: 469px;
    font-size: 42px;
    line-height: 50px;
    letter-spacing: 8px;
  }
  .quote--journey {
    top: 529px;
    font-family: "Yesteryear", cursive;
    font-size: 64px;
    line-height: 72px;
    display: flex;
    justify-content: center;
    align-items: center;
    gap: 10px;
  }
  .swash {
    width: 74px;
    height: 24px;
  }
  .swash path {
    fill: none;
    stroke: var(--ink);
    stroke-width: 5;
    stroke-linecap: round;
  }
  .quote--moment {
    top: 598px;
    font-family: "Libre Baskerville", serif;
    font-weight: 700;
    font-size: 55px;
    line-height: 64px;
  }
  .divider {
    position: absolute;
    left: 200px;
    top: 666px;
    width: 936px;
    border-top: 2px dashed var(--ink);
  }
  .quote--bowl {
    top: 673px;
    font-size: 40px;
    line-height: 48px;
    letter-spacing: 6px;
  }
  .quote--dreams {
    top: 728px;
    font-family: "Yesteryear", cursive;
    font-size: 76px;
    line-height: 84px;
  }
  .star {
    font-family: serif;
    font-size: 32px;
    vertical-align: 14px;
    margin: 0 18px;
  }
</style>
</head>
<body>
  <main class="poster">
    <div class="bicycle" role="img" aria-label="Photograph of a black single-speed bicycle mounted on the wall, facing right"></div>

    <p class="quote quote--caps quote--race">Life is not a race</p>

    <p class="quote quote--journey">
      <svg class="swash" viewBox="0 0 74 24" aria-hidden="true"><path d="M4 16 C16 2, 30 4, 38 12 S60 22, 70 8"/></svg>
      <span>It is a journey</span>
      <svg class="swash" viewBox="0 0 74 24" aria-hidden="true"><path d="M4 16 C12 2, 34 4, 42 12 S58 22, 70 8"/></svg>
    </p>

    <p class="quote quote--moment">Enjoy each moment. Relax!</p>

    <div class="divider"></div>

    <p class="quote quote--caps quote--bowl">Have a bowl of Bun and Bite</p>

    <p class="quote quote--dreams"><span class="star">★</span>Make all your dreams come true<span class="star">★</span></p>
  </main>
</body>
</html>
```